International business needs business cards

Our company, DRV Ventures Inc. is in the business of supplying a range construction products with particular emphasis on CEMENT. We have developed our own brand - TORVAN SUPPLIES - with which to infiltrate the market. We are launching our brand of cement (TORVAN Type IS Cement) into the Caribbean which is unlike anything this market has ever seen. A monopoly has existed here for the past 60-odd years and the market has now opened to allow the importation of other brands and consumers are anxious and ready for change/improvement. We are very excited to be launching and want to make a great first impression. We will be conducting workshops and seminars (from government level to the hardware store owners) and we want our business card to give us the strong, confident introduction that we need.

Target Market(s)

construction; builders; engineers; home owners

Industry/Entity Type

Construction

Contact Information for Business Card

Marisol Depree
CEO
cell # 1 555 4180736
Ground floor,Lindell Plaza Suite 2734
Port Halden,Isla Verra
Verra Isles,KY1-4823
EMAIL: m.depree@drvventuresinc.example
web site drvventuresinc.example

COMPANY: skype info drv.ventures.example

second card
Yvette Brannock-Depree
CFO
CELL# 1 555 607 3941
Port Halden,Isla Verra
Verra Isles,KY1-4823
EMAIL: y.brannockdepree@drvventuresinc.example
website drvventuresinc.example

Requirements
Must have
• Business cards must display BOTH logos - DRV is the company and TORVAN is the brand.

```html
<!DOCTYPE html>
<html lang="en">
<head>
<meta charset="UTF-8">
<title>DRV Ventures Inc. – Business Cards</title>
<link rel="stylesheet" href="https://fonts.googleapis.com/css2?family=Open+Sans:wght@400;600;700&display=swap">
<style>
  :root {
    --page-bg: #e9e6e1;
    --card-white: #ffffff;
    --card-black: #0b0b0b;
    --card-black-soft: #222222;
    --brand-red: #8e1a1c;
    --brand-red-dark: #6e1012;
    --ink: #1a1a1a;
    --ink-grey: #6a6a6a;
    --edge-grey: #5c5c5c;
    --panel-text: #ffffff;
    --panel-soft: #f1dede;
  }
  * { margin: 0; padding: 0; box-sizing: border-box; }
  html, body {
    width: 1200px; height: 843px; overflow: hidden;
    background: var(--page-bg);
    font-family: "Open Sans", Arial, sans-serif;
  }
  .canvas { position: relative; width: 1200px; height: 843px; }
  .card {
    position: absolute; left: 320px; width: 560px; height: 320px;
    overflow: hidden;
    box-shadow: 0 6px 18px rgba(0,0,0,0.18);
  }

  /* Back card */
  .card-back {
    top: 70px;
    background: linear-gradient(160deg, var(--card-black-soft) 0%, var(--card-black) 55%);
  }
  .back-mark {
    position: absolute; left: 50%; top: 128px; transform: translateX(-50%);
    display: flex; align-items: center; gap: 14px; white-space: nowrap;
  }
  .back-mark .mark-square { width: 62px; height: 62px; background: var(--brand-red); flex: none; }
  .back-mark .mark-name { color: #ffffff; font-weight: 700; font-size: 26px; letter-spacing: 1px; }
  .back-web {
    position: absolute; left: 40px; bottom: 34px;
    color: #bdbdbd; font-size: 13px; letter-spacing: 3px;
  }

  /* Front card */
  .card-front { top: 450px; background: var(--card-white); }
  .edge-band {
    position: absolute; left: 0; top: 0; width: 16px; height: 100%;
    background: var(--edge-grey);
  }
  .company-mark {
    position: absolute; left: 46px; top: 48px;
    display: flex; align-items: center; gap: 10px; white-space: nowrap;
  }
  .company-mark .mark-square { width: 52px; height: 52px; background: var(--brand-red); flex: none; }
  .company-mark .mark-text { color: var(--ink); font-weight: 700; line-height: 1; }
  .company-mark .mark-main { font-size: 40px; letter-spacing: 1px; display: block; }
  .company-mark .mark-sub { font-size: 12px; letter-spacing: 1px; display: block; margin-top: 4px; }

  .brand-mark {
    position: absolute; left: 62px; top: 150px;
    display: flex; align-items: center; gap: 10px; white-space: nowrap;
  }
  .brand-mark .mark-circle { width: 64px; height: 64px; border-radius: 50%; background: var(--ink-grey); flex: none; }
  .brand-mark .mark-name { color: var(--ink-grey); font-weight: 700; font-size: 22px; letter-spacing: 2px; }

  .contact-panel {
    position: absolute; left: 282px; top: 44px; right: 0; bottom: 40px;
    background: linear-gradient(135deg, var(--brand-red) 0%, var(--brand-red-dark) 100%);
    color: var(--panel-text);
    padding: 14px 16px 0 22px;
  }
  .person-name { font-weight: 700; font-size: 18px; line-height: 1.2; }
  .person-title { font-size: 12px; color: var(--panel-soft); margin-bottom: 8px; }
  .address { font-size: 12.5px; line-height: 1.3; margin-bottom: 6px; }
  .contact-line {
    display: flex; align-items: center; gap: 8px;
    font-size: 12.5px; line-height: 1.55; white-space: nowrap;
  }
  .contact-line svg { width: 12px; height: 12px; flex: none; }
</style>
</head>
<body>
<main class="canvas">

  <section class="card card-back" aria-label="Business card back">
    <div class="back-mark">
      <span class="mark-square"></span>
      <span class="mark-name">DRV Ventures Inc.</span>
    </div>
    <p class="back-web">www.drvventuresinc.example</p>
  </section>

  <section class="card card-front" aria-label="Business card front">
    <div class="edge-band"></div>

    <div class="company-mark">
      <span class="mark-square"></span>
      <span class="mark-text">
        <span class="mark-main">DRV</span>
        <span class="mark-sub">VENTURES INC.</span>
      </span>
    </div>

    <div class="brand-mark">
      <span class="mark-circle"></span>
      <span class="mark-name">TORVAN</span>
    </div>

    <div class="contact-panel">
      <p class="person-name">Marisol Depree</p>
      <p class="person-title">CEO</p>
      <p class="address">Street level<br>Lindell Plaza Suite 2734<br>Port Halden,Isla Verra<br>Verra Isles,VR2-4823</p>
      <p class="contact-line">
        <svg viewBox="0 0 12 12" aria-hidden="true"><rect x="3" y="0.5" width="6" height="11" rx="1" fill="none" stroke="#fff" stroke-width="1.2"/><circle cx="6" cy="9.5" r="0.7" fill="#fff"/></svg>
        1 555 4180736
      </p>
      <p class="contact-line">
        <svg viewBox="0 0 12 12" aria-hidden="true"><rect x="0.6" y="2" width="10.8" height="8" fill="none" stroke="#fff" stroke-width="1.2"/><path d="M0.6 2 L6 6.5 L11.4 2" fill="none" stroke="#fff" stroke-width="1.2"/></svg>
        m.depree@drvventuresinc.example
      </p>
      <p class="contact-line">
        <svg viewBox="0 0 12 12" aria-hidden="true"><circle cx="6" cy="6" r="5.3" fill="none" stroke="#fff" stroke-width="1.2"/><ellipse cx="6" cy="6" rx="2.3" ry="5.3" fill="none" stroke="#fff" stroke-width="1"/><path d="M0.8 6 H11.2" stroke="#fff" stroke-width="1"/></svg>
        www.drvventuresinc.example
      </p>
    </div>
  </section>

</main>
</body>
</html>
```